VOMRA Pty Ltd Business Card

Looking for a simple yet eye-catching double-sided business card design using my company logo on one side and contact details on the other.

Target Market(s)

Government

Industry/Entity Type

Communication Systems Engineering

Contact Information for Business Card

VOMRA Pty Ltd

Requirements
Nice to have
• Would be great to have a QR code so details can be scanned into contacts

```html
<!DOCTYPE html>
<html lang="en">
<head>
<meta charset="UTF-8">
<title>VOMRA Pty Ltd Business Card</title>
<link href="https://fonts.googleapis.com/css2?family=Open+Sans:wght@400;700;800&display=swap" rel="stylesheet">
<style>
  :root {
    --stage: #232323;
    --slate: #37424a;
    --paper: #ffffff;
    --ink: #1f2529;
    --mist: #e9ebec;
    --mist-deep: #dcdfe1;
  }
  * { box-sizing: border-box; margin: 0; padding: 0; }
  html, body {
    width: 1200px; height: 780px; overflow: hidden;
    background: var(--stage);
    font-family: "Open Sans", sans-serif;
  }
  .canvas {
    position: relative; width: 1200px; height: 780px;
    display: flex; align-items: center; justify-content: center; gap: 40px;
  }
  .card {
    position: relative; width: 560px; height: 320px; overflow: hidden;
    box-shadow: 0 10px 30px rgba(0,0,0,.45);
  }
  /* Logo side */
  .card--logo { background: var(--slate); display: flex; align-items: center; justify-content: center; }
  .brand { display: flex; align-items: center; gap: 22px; }
  .brand__dot { width: 54px; height: 54px; border-radius: 50%; background: currentColor; }
  .brand__name { font-weight: 800; letter-spacing: 4px; line-height: 1; }
  .card--logo .brand { color: var(--paper); }
  .card--logo .brand__name { font-size: 72px; }

  /* Details side */
  .card--details { background: var(--paper); color: var(--ink); }
  .card__decoration {
    position: absolute; right: 0; top: 0; width: 300px; height: 100%;
    background: radial-gradient(ellipse at 55% 45%, var(--mist-deep) 0%, var(--mist) 45%, var(--paper) 78%);
    opacity: .7;
  }
  .card--details .brand { position: absolute; left: 34px; top: 58px; color: var(--slate); gap: 16px; }
  .card--details .brand__dot { width: 40px; height: 40px; }
  .card--details .brand__name { font-size: 46px; }

  .holder { position: absolute; right: 30px; top: 82px; text-align: right; }
  .holder__name { font-size: 30px; font-weight: 700; color: var(--slate); line-height: 1.1; }
  .holder__role { font-size: 14px; color: var(--ink); margin-top: 2px; }
  .holder__bar { position: absolute; right: 0; top: 80px; width: 14px; height: 46px; background: var(--slate); }

  .contact { position: absolute; left: 34px; bottom: 26px; font-size: 15px; line-height: 1.3; }
  .contact__address { margin-bottom: 12px; }
  .contact__list { list-style: none; }
  .contact__item { display: flex; align-items: center; gap: 10px; }
  .contact__icon { width: 14px; height: 14px; fill: var(--slate); flex: none; }
</style>
</head>
<body>
<main class="canvas">
  <section class="card card--logo" aria-label="Card back">
    <div class="brand">
      <span class="brand__dot"></span>
      <span class="brand__name">VOMRA</span>
    </div>
  </section>

  <section class="card card--details" aria-label="Card front">
    <div class="card__decoration" role="img" aria-label="Faint brand symbol decoration"></div>
    <div class="brand">
      <span class="brand__dot"></span>
      <span class="brand__name">VOMRA</span>
    </div>

    <div class="holder">
      <p class="holder__name">Jordan Hale</p>
      <p class="holder__role">Co-Founder</p>
    </div>
    <span class="holder__bar"></span>

    <div class="contact">
      <p class="contact__address">24-26 Harbour Lane Millers<br>Point NSW 2000 Australia</p>
      <ul class="contact__list">
        <li class="contact__item">
          <svg class="contact__icon" viewBox="0 0 24 24"><path d="M6.6 10.8a15.1 15.1 0 0 0 6.6 6.6l2.2-2.2c.3-.3.7-.4 1-.2 1.1.4 2.3.6 3.6.6.6 0 1 .4 1 1V20c0 .6-.4 1-1 1A17 17 0 0 1 3 4c0-.6.4-1 1-1h3.5c.6 0 1 .4 1 1 0 1.3.2 2.5.6 3.6.1.3 0 .7-.2 1z"/></svg>
          <span>(555) 210-4836</span>
        </li>
        <li class="contact__item">
          <svg class="contact__icon" viewBox="0 0 24 24"><circle cx="12" cy="12" r="10"/><path d="M2 12h20M12 2c3 3 3 17 0 20M12 2c-3 3-3 17 0 20" stroke="#fff" stroke-width="1.4" fill="none"/></svg>
          <span>www.vomra.com.au</span>
        </li>
        <li class="contact__item">
          <svg class="contact__icon" viewBox="0 0 24 24"><path d="M2 5h20v14H2z"/><path d="M2 5l10 8 10-8" stroke="#fff" stroke-width="1.6" fill="none"/></svg>
          <span>admin@vomra.com.au</span>
        </li>
      </ul>
    </div>
  </section>
</main>
</body>
</html>
```